Salon and Spa Distributor Business Card

Need a business card. We are are distributor in the salon and spa industry. We identify with natural beauty. Need a card with:
Company Name: Petal Quarry"
Title: "President & CEO"
Address
Company Phone number
email
website
Tag Line:" The Professional Salon Source"

Industry/Entity Type

Business

Contact Information for Business Card

Name: Dov Strommen
Title: "President & CEO"
Address: 31 Harlow Ln, Bexmoor, NJ 07813
Company Phone number: 800-463-5918
email: dovstrommen@petalquarry.example
website: www.petalquarry.example

Requirements
Should not have
• No black backgrounds

```html
<!DOCTYPE html>
<html lang="en">
<head>
<meta charset="utf-8">
<title>Petal Quarry Business Card</title>
<link rel="stylesheet" href="https://fonts.googleapis.com/css2?family=Questrial&family=Tinos:ital,wght@0,400;1,400;1,700&display=swap">
<style>
  :root {
    --backdrop: #ececec;
    --green-dark: #0e6a36;
    --green-mid: #3f9c3f;
    --green-light: #6abd45;
    --green-text: #3a9a3c;
    --card-white: #f7f7f7;
    --swoosh-grey: #a4a4a4;
    --ink: #1c1c1c;
    --white: #ffffff;
  }
  * { margin: 0; padding: 0; box-sizing: border-box; }
  html, body { width: 1200px; height: 586px; overflow: hidden; }
  body {
    position: relative;
    background: var(--backdrop);
    font-family: "Questrial", "Century Gothic", sans-serif;
  }
  .card {
    position: absolute;
    top: 128px;
    width: 501px;
    height: 301px;
    overflow: hidden;
  }

  /* Front */
  .card-front {
    left: 61px;
    background: linear-gradient(90deg, var(--green-dark) 0%, var(--green-mid) 25%, var(--green-light) 50%, var(--green-mid) 75%, var(--green-dark) 100%);
    color: var(--white);
  }
  .front-mark {
    position: absolute;
    left: 0; right: 0;
    top: 40px;
    display: flex;
    flex-direction: column;
    align-items: center;
    gap: 18px;
  }
  .front-mark .mark-dot {
    width: 88px; height: 88px;
    border-radius: 50%;
    background: var(--white);
  }
  .front-mark .mark-name {
    font-size: 32px;
    line-height: 1;
  }
  .front-web {
    position: absolute;
    top: 240px;
    left: 0; right: 0;
    display: flex;
    justify-content: center;
    align-items: center;
    gap: 8px;
    font-size: 13px;
  }
  .front-web .rule {
    width: 59px;
    height: 2px;
    background: var(--white);
  }
  .tagline {
    position: absolute;
    top: 264px;
    left: 0; right: 0;
    text-align: center;
    font-family: "Tinos", "Times New Roman", serif;
    font-style: italic;
    font-weight: 700;
    font-size: 12.5px;
    letter-spacing: 4.2px;
    color: var(--ink);
  }

  /* Back */
  .card-back {
    left: 619px;
    background: var(--card-white);
  }
  .back-brand {
    position: absolute;
    top: 40px;
    right: 24px;
    display: flex;
    align-items: center;
    gap: 12px;
  }
  .back-brand .mark-dot {
    width: 44px; height: 44px;
    border-radius: 50%;
    background: var(--green-text);
  }
  .back-brand .mark-name {
    font-size: 25px;
    color: var(--green-text);
  }
  .person {
    position: absolute;
    left: 29px;
    top: 124px;
  }
  .person-name {
    font-size: 16px;
    color: var(--green-text);
  }
  .person-title {
    margin-top: 3px;
    font-family: "Tinos", "Times New Roman", serif;
    font-style: italic;
    font-size: 11px;
    color: var(--ink);
  }
  .contact-list {
    position: absolute;
    left: 28px;
    top: 187px;
    list-style: none;
  }
  .contact-list li {
    display: flex;
    align-items: center;
    gap: 6px;
    height: 24px;
    font-size: 12px;
    color: var(--ink);
  }
  .contact-icon {
    width: 18px; height: 18px;
    flex: none;
  }
  .back-swoosh {
    position: absolute;
    left: 0; top: 0;
  }
</style>
</head>
<body>

  <section class="card card-front">
    <div class="front-mark">
      <span class="mark-dot"></span>
      <span class="mark-name">Petal Quarry</span>
    </div>
    <div class="front-web">
      <span class="rule"></span>
      <span>www.petalquarry.example</span>
      <span class="rule"></span>
    </div>
    <p class="tagline">The Professional Salon Source</p>
  </section>

  <section class="card card-back">
    <svg class="back-swoosh" width="501" height="301" viewBox="0 0 501 301">
      <defs>
        <linearGradient id="band-green" x1="0" y1="0" x2="1" y2="0">
          <stop offset="0" stop-color="var(--green-dark)"/>
          <stop offset="0.5" stop-color="var(--green-light)"/>
          <stop offset="1" stop-color="var(--green-dark)"/>
        </linearGradient>
      </defs>
      <path d="M110 280 Q 380 276 501 229 L501 246 Q 380 279 110 280 Z" fill="var(--swoosh-grey)"/>
      <path d="M0 285 L140 285 Q 380 282 501 253 L501 301 L0 301 Z" fill="url(#band-green)"/>
    </svg>

    <div class="back-brand">
      <span class="mark-dot"></span>
      <span class="mark-name">Petal Quarry</span>
    </div>

    <div class="person">
      <p class="person-name">Dov Strommen</p>
      <p class="person-title">President &amp; CEO</p>
    </div>

    <ul class="contact-list">
      <li>
        <svg class="contact-icon" viewBox="0 0 18 18" aria-hidden="true">
          <circle cx="9" cy="9" r="9" fill="var(--green-text)"/>
          <path d="M5 7.5 Q9 4 13 7.5 L12 9 L10.5 8 L10.5 7 Q9 6.5 7.5 7 L7.5 8 L6 9 Z M6 10 H12 V13 H6 Z" fill="var(--white)"/>
        </svg>
        <span>800-463-5918</span>
      </li>
      <li>
        <svg class="contact-icon" viewBox="0 0 18 18" aria-hidden="true">
          <circle cx="9" cy="9" r="9" fill="var(--green-text)"/>
          <rect x="4.5" y="6" width="9" height="6.5" fill="none" stroke="var(--white)" stroke-width="1.2"/>
          <path d="M4.5 6 L9 9.8 L13.5 6" fill="none" stroke="var(--white)" stroke-width="1.2"/>
        </svg>
        <span>dovstrommen@petalquarry.example</span>
      </li>
      <li>
        <svg class="contact-icon" viewBox="0 0 18 18" aria-hidden="true">
          <circle cx="9" cy="9" r="9" fill="var(--green-text)"/>
          <path d="M9 14.5 C6.5 11 5.5 9.5 5.5 7.8 A3.5 3.5 0 0 1 12.5 7.8 C12.5 9.5 11.5 11 9 14.5 Z" fill="var(--white)"/>
          <circle cx="9" cy="7.8" r="1.4" fill="var(--green-text)"/>
        </svg>
        <span>31 Harlow Ln, Bexmoor, NJ 07813</span>
      </li>
    </ul>
  </section>

</body>
</html>
```